Exciting Clear Cup Design!

We are a thriving breakfast, lunch and pastry shop that encourages our guests to drink water instead of soda, and wanted to find a way to add value by giving our guests a clear disposable yet reuseable cup with water, instead of the glassware we are currently using. We want them to be able to take the cup with them.
I would like to include a maybe a character or a drawing of water or a cup full of water.
I really like the verandoro bags, and I often save the clear cups from brimwell that are technically disposable but nice to have at my desk as a refillable water cup with a lid. Check out our website, TovarisCafe.example, so you can see our brand. We are locally owned, a busy mom and pop cafe, and want the design to include our logo as well as something cool or cute or catchy.

Target Market(s)

affluent professionals, health conscious people, foodies

Industry/Entity Type

Shop

Requirements
Must have
• our logo
Nice to have
• (just ideas)
a catchy phrase
drink water
one of your 8 glasses

```html
<!DOCTYPE html>
<html lang="en">
<head>
<meta charset="utf-8">
<title>Tovaris Clear Cup</title>
<link rel="stylesheet" href="https://fonts.googleapis.com/css2?family=Cinzel:wght@400&family=Lato:wght@400&display=swap">
<style>
  :root {
    --canvas: #ffffff;
    --outline: #1a1a1a;
    --teal: #6fcdd1;
    --teal-light: #a9e0e3;
    --teal-pale: #e3f5f6;
    --brown: #5a3a1e;
  }
  html, body {
    margin: 0;
    width: 1200px;
    height: 709px;
    overflow: hidden;
    background: var(--canvas);
  }
  .cup-sheet { display: block; width: 1200px; height: 709px; }
  .cup-outline { fill: none; stroke: var(--outline); stroke-width: 2; stroke-linejoin: round; }
  .print-edge { stroke: var(--outline); stroke-width: 1.6; }
  .ornament-band { fill: url(#ornament-tone); }
  .brand-dot { fill: var(--teal); }
  .brand-name { font-family: "Cinzel", serif; font-size: 46px; fill: var(--teal); letter-spacing: 1px; }
  .brand-tagline { font-family: "Cinzel", serif; font-size: 16px; fill: var(--teal); letter-spacing: 0.5px; }
  .water-art-area { fill: url(#water-tone); }
  .slogan { font-family: "Lato", sans-serif; font-size: 25px; letter-spacing: 0.5px; }
  .slogan-drink { fill: var(--brown); }
  .slogan-smart { fill: var(--teal); }
</style>
</head>
<body>
<svg class="cup-sheet" viewBox="0 0 1200 709" xmlns="http://www.w3.org/2000/svg">
  <defs>
    <linearGradient id="ornament-tone" x1="0" y1="0" x2="1" y2="0">
      <stop offset="0" stop-color="var(--teal-light)"/>
      <stop offset="0.5" stop-color="var(--teal-pale)"/>
      <stop offset="1" stop-color="var(--teal-light)"/>
    </linearGradient>
    <linearGradient id="water-tone" x1="0" y1="0" x2="0" y2="1">
      <stop offset="0" stop-color="var(--teal-light)"/>
      <stop offset="1" stop-color="var(--teal)"/>
    </linearGradient>
    <path id="cup-shape" d="M232,140 Q238,125 390,124 Q544,125 548,138 Q551,155 540,165 L492,470 Q486,500 490,520 Q485,540 480,550 L476,580 Q455,577 390,584 Q330,583 315,574 L300,545 Q296,500 290,470 L246,165 Q230,152 232,140 Z"/>
  </defs>

  <g class="cup cup-front">
    <use href="#cup-shape" class="cup-outline"/>
    <line class="print-edge" x1="255" y1="188" x2="527" y2="188"/>
    <line class="print-edge" x1="289" y1="467" x2="490" y2="467"/>
    <rect class="ornament-band" x="278" y="212" width="219" height="29" rx="14" role="img" aria-label="Row of fork, knife and spoon icons alternating with teal swirl flourishes"/>
    <circle class="brand-dot" cx="392" cy="291" r="40"/>
    <text class="brand-name" x="390" y="382" text-anchor="middle">Tovaris</text>
    <text class="brand-tagline" x="392" y="406" text-anchor="middle">Real Food Kitchen</text>
    <rect class="ornament-band" x="288" y="421" width="206" height="26" rx="13" role="img" aria-label="Row of fork, knife and spoon icons alternating with teal swirl flourishes"/>
  </g>

  <g class="cup cup-back" transform="translate(420 0)">
    <use href="#cup-shape" class="cup-outline"/>
    <line class="print-edge" x1="255" y1="188" x2="527" y2="188"/>
    <line class="print-edge" x1="289" y1="475" x2="492" y2="475"/>
    <rect class="ornament-band" x="285" y="210" width="215" height="28" rx="14" role="img" aria-label="Row of fork, knife and spoon icons alternating with teal swirl flourishes"/>
    <rect class="water-art-area" x="358" y="240" width="92" height="110" rx="6" role="img" aria-label="Illustration of a glass of water with a bendy straw and rising bubbles"/>
    <text class="slogan slogan-drink" x="392" y="386" text-anchor="middle">DRINK</text>
    <text class="slogan slogan-smart" x="392" y="412" text-anchor="middle">SMART</text>
    <rect class="ornament-band" x="287" y="421" width="206" height="26" rx="13" role="img" aria-label="Row of fork, knife and spoon icons alternating with teal swirl flourishes"/>
  </g>
</svg>
</body>
</html>
```